Software Development Consulting Company Needs Business Card Design

We need a new business card design for our consultants at Kestrel Works (kestrelworks.example). We are a small firm that provides high-end software development and methodology consulting to medium to large enterprise IT organizations.

Our logo uses Futura for the font and we would like to stick with navy blue and canary yellow for the logo colors. Attached are normal and reversed versions of our logos in illustrator format.
Updates

Hi Everyone, Thank yo very much for your amazing design ideas. I have created a poll for this project and our employees will be voting on the design they wish to use. We will be making a decision this Wednesday (October 22nd). Thanks again, Dale Hartwick

Industry/Entity Type

Business

```html
<!DOCTYPE html>
<html lang="en">
<head>
<meta charset="utf-8">
<title>Kestrel Works — Business Card</title>
<link rel="stylesheet" href="https://fonts.googleapis.com/css2?family=Jost:wght@500&family=Open+Sans:wght@400;700&display=swap">
<style>
  :root {
    --navy: #1f4a72;
    --canary: #fff000;
    --ink: #2b2b2b;
    --paper: #ffffff;
    --backdrop: #e9e9ee;
    --rule: #b9b9b9;
  }
  * { box-sizing: border-box; margin: 0; padding: 0; }
  html, body { width: 1200px; height: 980px; overflow: hidden; }
  body {
    background: var(--backdrop);
    font-family: "Open Sans", Arial, sans-serif;
    display: flex;
    flex-direction: column;
    align-items: center;
    justify-content: space-evenly;
  }
  .card {
    position: relative;
    width: 780px;
    height: 446px;
    border-radius: 36px;
    overflow: hidden;
    box-shadow: 0 6px 18px rgba(0,0,0,0.12);
  }
  .card--front { background: var(--paper); }
  .card--back { background: var(--canary); }

  .wordmark {
    font-family: "Jost", "Futura", sans-serif;
    font-weight: 500;
    color: var(--navy);
    letter-spacing: 6px;
    text-transform: uppercase;
    display: flex;
    align-items: center;
    gap: 16px;
  }
  .wordmark__dot {
    width: 22px; height: 22px;
    border: 4px solid var(--navy);
    border-radius: 50%;
  }
  .card--front .wordmark {
    position: absolute;
    top: 78px; left: 0; right: 0;
    justify-content: center;
    font-size: 58px;
  }

  .contact {
    position: absolute;
    top: 210px; left: 0; right: 0;
    display: flex;
    justify-content: center;
  }
  .contact__person {
    text-align: right;
    padding-right: 22px;
    border-right: 1.5px solid var(--rule);
    color: var(--ink);
  }
  .contact__name { font-weight: 700; color: var(--navy); font-size: 26px; line-height: 1.2; }
  .contact__title { font-size: 18px; margin-bottom: 10px; }
  .contact__place { font-size: 17px; display: flex; align-items: center; gap: 8px; justify-content: flex-end; }
  .contact__lines {
    padding-left: 22px;
    list-style: none;
    font-size: 19px;
    color: var(--ink);
    padding-top: 14px;
  }
  .contact__lines li { display: flex; align-items: center; gap: 10px; margin-bottom: 6px; }
  .icon { width: 18px; height: 18px; flex: none; }

  .wave { position: absolute; left: 0; bottom: 0; width: 780px; height: 446px; }

  .card--back .wordmark {
    position: absolute;
    top: 170px; left: 0; right: 0;
    justify-content: center;
    font-size: 64px;
  }
  .back__web {
    position: absolute;
    bottom: 110px; left: 0; right: 0;
    text-align: center;
    font-weight: 700;
    font-size: 24px;
    letter-spacing: 5px;
    color: var(--navy);
  }
</style>
</head>
<body>

<section class="card card--front" aria-label="Business card front">
  <svg class="wave" viewBox="0 0 780 446" aria-hidden="true">
    <path d="M0,305 C150,330 270,420 560,446 L0,446 Z" fill="var(--canary)"/>
    <path d="M0,268 C150,292 270,395 650,446 L605,446 C275,412 150,318 0,298 Z" fill="var(--navy)"/>
    <path d="M210,330 C300,380 400,430 520,446" stroke="var(--navy)" stroke-width="2" fill="none"/>
  </svg>

  <div class="wordmark"><span class="wordmark__dot"></span>Kestrel Works</div>

  <div class="contact">
    <div class="contact__person">
      <p class="contact__name">Your Name</p>
      <p class="contact__title">Title</p>
      <p class="contact__place">
        <svg class="icon" viewBox="0 0 24 24"><path d="M12 2a7 7 0 0 0-7 7c0 5 7 13 7 13s7-8 7-13a7 7 0 0 0-7-7zm0 9.5A2.5 2.5 0 1 1 12 6.5a2.5 2.5 0 0 1 0 5z" fill="var(--navy)"/></svg>
        Lakeport, Fairhaven, IL
      </p>
    </div>
    <ul class="contact__lines">
      <li>
        <svg class="icon" viewBox="0 0 24 24"><circle cx="12" cy="12" r="11" fill="var(--navy)"/><path d="M8.5 6.5l2 2-1 1.5c.8 1.6 2 2.8 3.5 3.5l1.5-1 2 2-1.5 2c-4 0-8.5-4.5-8.5-8.5z" fill="#fff"/></svg>
        012-345-6789
      </li>
      <li>
        <svg class="icon" viewBox="0 0 24 24"><rect x="2" y="5" width="20" height="14" rx="2" fill="var(--navy)"/><path d="M3 6l9 7 9-7" stroke="#fff" stroke-width="2" fill="none"/></svg>
        info@kestrelworks.example
      </li>
      <li>
        <svg class="icon" viewBox="0 0 24 24"><circle cx="12" cy="12" r="10" fill="none" stroke="var(--navy)" stroke-width="2"/><path d="M2 12h20M12 2c3 3 3 17 0 20M12 2c-3 3-3 17 0 20" stroke="var(--navy)" stroke-width="1.5" fill="none"/></svg>
        www.kestrelworks.example
      </li>
    </ul>
  </div>
</section>

<section class="card card--back" aria-label="Business card back">
  <div class="wordmark"><span class="wordmark__dot"></span>Kestrel Works</div>
  <p class="back__web">www.kestrelworks.example</p>
</section>

</body>
</html>
```